Tovel & Associates - London New Letting and Property Management Company *

Tovel & Associates LTD is a new company based in London, and works with brand new residential property in the city centre.

We are aiming to have 1000 new properties a year.

We are looking for something modern and minimalistic :
Logo ,Monogram, Paper Head and Business Card.

Target Market(s)

Internation landlords

Industry/Entity Type

Real Estate

Logo Text

Tovel & Associates

Colors

Designer to choose colors to be used in the design.

Requirements
Nice to have
• A particular monogram with "TA"
Should not have
• Little House over the logo

```html
<!DOCTYPE html>
<html lang="en">
<head>
<meta charset="utf-8">
<title>Tovel &amp; Associates – Business Card</title>
<link href="https://fonts.googleapis.com/css2?family=Montserrat:wght@400;500;700&display=swap" rel="stylesheet">
<style>
  :root {
    --brand-blue: #0b6fb8;
    --brand-blue-dark: #0a5a98;
    --ink: #3a3a3a;
    --ink-soft: #6b6b6b;
    --rule: #8a8a8a;
    --paper: #ffffff;
    --paper-shade: #f1f1f1;
    --backdrop: #e4e6e9;
    --logo-light: #d9dde2;
  }
  * { box-sizing: border-box; margin: 0; padding: 0; }
  html, body {
    width: 1200px; height: 900px; overflow: hidden;
    background: var(--backdrop);
    font-family: "Montserrat", sans-serif;
  }
  .canvas {
    position: relative; width: 1200px; height: 900px;
    display: flex; flex-direction: column; align-items: center; justify-content: center; gap: 56px;
  }
  .card {
    position: relative; width: 620px; height: 354px;
    border-radius: 18px; overflow: hidden;
    box-shadow: 0 10px 28px rgba(0,0,0,.18);
  }
  /* Front */
  .card-front { background: linear-gradient(135deg, var(--paper-shade), var(--paper) 45%); }
  .person { position: absolute; left: 44px; top: 48px; }
  .person-name { color: var(--brand-blue); font-weight: 700; font-size: 24px; }
  .person-role { color: var(--ink-soft); font-size: 15px; margin-top: 2px; }
  .divider {
    position: absolute; left: 44px; right: 36px; top: 122px;
    height: 1.5px; background: var(--rule);
  }
  .contacts { position: absolute; left: 44px; top: 138px; list-style: none; }
  .contacts li {
    display: flex; align-items: center; gap: 10px;
    color: var(--ink); font-size: 15px; line-height: 24px;
  }
  .contacts svg { width: 13px; height: 13px; flex: none; }
  .wordmark {
    position: absolute; right: 40px; top: 56px;
    display: flex; align-items: center; gap: 12px;
  }
  .wordmark-square { width: 22px; height: 22px; background: var(--brand-blue); }
  .wordmark-name { color: var(--ink); font-weight: 700; font-size: 24px; line-height: 1.15; text-align: right; }
  .address {
    position: absolute; right: 40px; top: 140px;
    color: var(--ink); font-size: 15px; line-height: 22px; text-align: right;
  }
  .band-dark {
    position: absolute; left: 0; bottom: 0; width: 200px; height: 46px;
    background: var(--ink);
    clip-path: polygon(0 0, 100% 100%, 0 100%);
  }
  .band-blue {
    position: absolute; right: 0; bottom: 0; width: 480px; height: 46px;
    background: var(--brand-blue);
    clip-path: polygon(0 0, 100% 0, 100% 100%, 12% 100%);
    display: flex; align-items: center; justify-content: flex-end; padding-right: 40px;
  }
  .website { color: var(--paper); font-size: 16px; font-weight: 500; }
  /* Back */
  .card-back {
    background: linear-gradient(135deg, var(--brand-blue), var(--brand-blue-dark));
    display: flex; align-items: center; justify-content: center;
  }
  .back-mark { display: flex; align-items: center; gap: 16px; }
  .back-mark-square { width: 30px; height: 30px; background: var(--logo-light); }
  .back-mark-name { color: var(--logo-light); font-weight: 700; font-size: 36px; line-height: 1.15; text-align: right; }
</style>
</head>
<body>
<main class="canvas">
  <section class="card card-front" aria-label="Business card front">
    <div class="person">
      <h1 class="person-name">Elias Harwood</h1>
      <p class="person-role">Realtor</p>
    </div>
    <div class="divider"></div>
    <ul class="contacts">
      <li>
        <svg viewBox="0 0 14 14" aria-hidden="true"><rect x="3" y="1" width="8" height="12" rx="1.5" fill="none" stroke="#0b6fb8" stroke-width="1.6"/><line x1="6" y1="10.5" x2="8" y2="10.5" stroke="#0b6fb8" stroke-width="1.4"/></svg>
        020.555.0148
      </li>
      <li>
        <svg viewBox="0 0 14 14" aria-hidden="true"><path d="M3 1.5 L5.5 1.5 L6.3 4.5 L4.8 5.6 Q6 8.4 8.4 9.2 L9.5 7.7 L12.5 8.5 L12.5 11 Q12.5 12.5 11 12.5 Q2 12 1.5 3 Q1.5 1.5 3 1.5 Z" fill="#0b6fb8"/></svg>
        020.555.0192
      </li>
      <li>
        <svg viewBox="0 0 14 14" aria-hidden="true"><rect x="1" y="3" width="12" height="8.5" fill="none" stroke="#0b6fb8" stroke-width="1.4"/><polyline points="1,3 7,8 13,3" fill="none" stroke="#0b6fb8" stroke-width="1.4"/></svg>
        info@tovelassociates.com
      </li>
    </ul>
    <div class="wordmark">
      <span class="wordmark-square"></span>
      <span class="wordmark-name">Tovel &amp; Associates<br>LTD</span>
    </div>
    <address class="address" style="font-style:normal">48 Calder Row<br>Fenwick Park,<br>London EC2 7QX</address>
    <div class="band-dark"></div>
    <div class="band-blue"><span class="website">www.tovelassociates.com</span></div>
  </section>

  <section class="card card-back" aria-label="Business card back">
    <div class="back-mark">
      <span class="back-mark-square"></span>
      <span class="back-mark-name">Tovel &amp; Associates<br>LTD</span>
    </div>
  </section>
</main>
</body>
</html>
```